Business Card Design

Velora Pixel Outreach

An online marketing consulting & strategy business for the cosmetic niche

We specialise in Increasing Leads, Conversions & Content Marketing

I am looking for a very clean, BOLD business card that is simple & effective

Target Market(s)

cosmetic surgeons & cosmetic clinics

Industry/Entity Type

Marketing

Contact Information for Business Card

Dermot Kalway
Online Marketing Strategist

Dermot@VeloraPixelOutreach.example
0492 158 620

LinkedIn: in/dermotkalway

```html
<!DOCTYPE html>
<html lang="en">
<head>
<meta charset="utf-8">
<title>Velora Pixel Outreach – Business Card</title>
<link rel="stylesheet" href="https://fonts.googleapis.com/css2?family=Arimo:wght@400;700&display=swap">
<style>
  :root {
    --board: #afaeae;
    --card: #ffffff;
    --blue: #2fa9e0;
    --teal: #3bb3c3;
    --green: #9ccb3b;
    --green-soft: #a6cf4a;
    --ink: #58595b;
    --text: #4d4d4f;
    --shadow: rgba(0, 0, 0, 0.45);
  }
  * { box-sizing: border-box; margin: 0; padding: 0; }
  html, body { width: 1200px; height: 900px; overflow: hidden; }
  body {
    background: var(--board);
    font-family: "Arimo", Arial, sans-serif;
    position: relative;
  }
  .card {
    position: absolute;
    background: var(--card);
    box-shadow: 3px 3px 4px var(--shadow);
    overflow: hidden;
  }
  .card--rounded { border-radius: 22px; }

  /* front side */
  .front { left: 18px; width: 567px; }
  .front--square { top: 108px; height: 342px; }
  .front--rounded { top: 484px; height: 328px; }
  .front .brand {
    position: absolute; left: 313px; top: var(--brand-top);
    display: flex; align-items: center; gap: 10px;
  }
  .front--square { --brand-top: 234px; --bar-top: 314px; }
  .front--rounded { --brand-top: 222px; --bar-top: 302px; }
  .brand-dot {
    width: 62px; height: 62px; border-radius: 50%;
    background: linear-gradient(135deg, var(--blue), var(--green));
  }
  .wordmark {
    color: var(--ink); font-weight: 400;
    font-size: 26px; line-height: 27px; letter-spacing: 3px;
    text-transform: uppercase;
  }
  .wordmark span { display: block; }
  .name-bar {
    position: absolute; left: 266px; right: 0; top: var(--bar-top); bottom: 0;
    border-top-left-radius: 14px;
    background: linear-gradient(90deg, var(--green-soft), var(--green) 60%, var(--teal));
    display: flex; align-items: center; padding-left: 14px; color: #fff;
  }
  .name-bar .person { font-weight: 700; font-size: 17px; }
  .name-bar .role {
    font-weight: 700; font-size: 11px; margin-left: 5px;
    padding-left: 4px; border-left: 1px solid #fff; line-height: 18px;
  }

  /* back side */
  .back { left: 612px; width: 566px; }
  .back--square { top: 108px; height: 342px; --logo-top: 37px; --name-top: 146px; --contact-top: 218px; --row-gap: 32px; }
  .back--rounded { top: 484px; height: 328px; --logo-top: 36px; --name-top: 136px; --contact-top: 208px; --row-gap: 31px; }
  .accent-band {
    position: absolute; left: 0; top: 0; bottom: 0; width: 113px;
    background: linear-gradient(180deg, var(--blue) 5%, var(--green) 95%);
  }
  .accent-rule {
    position: absolute; left: 122px; top: 0; bottom: 0; width: 2px;
    background: var(--blue);
  }
  .back .brand {
    position: absolute; left: 48px; top: var(--logo-top);
    display: flex; align-items: center;
  }
  .brand-square { width: 86px; height: 96px; background: var(--card); }
  .back .wordmark { font-size: 31px; line-height: 28px; letter-spacing: 4px; margin-left: 16px; padding-top: 6px; }
  .identity { position: absolute; left: 128px; top: var(--name-top); }
  .identity .person {
    font-size: 21px; font-weight: 400; padding-bottom: 2px;
    border-bottom: 2px solid var(--blue); display: inline-block; padding-right: 2px;
  }
  .person .first { color: var(--blue); }
  .person .last { color: var(--green); }
  .identity .role { color: var(--green); font-size: 14px; font-weight: 700; margin-top: 6px; }
  .contacts { position: absolute; left: 144px; top: var(--contact-top); list-style: none; }
  .contacts li {
    display: flex; align-items: center; height: var(--row-gap);
    color: var(--text); font-size: 13.5px;
  }
  .contacts svg { width: 18px; height: 18px; margin-right: 10px; flex: none; }
</style>
</head>
<body>

  <!-- front, square corners -->
  <section class="card front front--square">
    <div class="brand">
      <div class="brand-dot"></div>
      <div class="wordmark"><span>Velora</span><span>Pixel</span><span>Outreach</span></div>
    </div>
    <div class="name-bar"><span class="person">Dermot Kalway</span><span class="role">Online Marketing Strategist</span></div>
  </section>

  <!-- back, square corners -->
  <section class="card back back--square">
    <div class="accent-band"></div>
    <div class="accent-rule"></div>
    <div class="brand">
      <div class="brand-square"></div>
      <div class="wordmark"><span>Velora</span><span>Pixel</span><span>Outreach</span></div>
    </div>
    <div class="identity">
      <div class="person"><span class="first">Dermot</span> <span class="last">Kalway</span></div>
      <div class="role">Online Marketing Strategist</div>
    </div>
    <ul class="contacts">
      <li><svg viewBox="0 0 18 18"><rect width="18" height="18" rx="2" fill="#2fa9e0"/><path d="M6 4h2l1 3-1.5 1a7 7 0 0 0 2.5 2.5L11 9l3 1v2a1.5 1.5 0 0 1-1.5 1.5A9 9 0 0 1 4.5 5.5 1.5 1.5 0 0 1 6 4z" fill="#fff"/></svg>0492 158 620</li>
      <li><svg viewBox="0 0 18 18"><rect width="18" height="18" rx="2" fill="#2fa9e0"/><rect x="3.5" y="5" width="11" height="8" fill="none" stroke="#fff" stroke-width="1.2"/><path d="M3.5 5l5.5 4.5L14.5 5" fill="none" stroke="#fff" stroke-width="1.2"/></svg>Dermot@VeloraPixelOutreach.example</li>
      <li><svg viewBox="0 0 18 18"><rect width="18" height="18" rx="2" fill="#2fa9e0"/></svg>in/dermotkalway</li>
    </ul>
  </section>

  <!-- front, rounded corners -->
  <section class="card card--rounded front front--rounded">
    <div class="brand">
      <div class="brand-dot"></div>
      <div class="wordmark"><span>Velora</span><span>Pixel</span><span>Outreach</span></div>
    </div>
    <div class="name-bar"><span class="person">Dermot Kalway</span><span class="role">Online Marketing Strategist</span></div>
  </section>

  <!-- back, rounded corners -->
  <section class="card card--rounded back back--rounded">
    <div class="accent-band"></div>
    <div class="accent-rule"></div>
    <div class="brand">
      <div class="brand-square"></div>
      <div class="wordmark"><span>Velora</span><span>Pixel</span><span>Outreach</span></div>
    </div>
    <div class="identity">
      <div class="person"><span class="first">Dermot</span> <span class="last">Kalway</span></div>
      <div class="role">Online Marketing Strategist</div>
    </div>
    <ul class="contacts">
      <li><svg viewBox="0 0 18 18"><rect width="18" height="18" rx="2" fill="#2fa9e0"/><path d="M6 4h2l1 3-1.5 1a7 7 0 0 0 2.5 2.5L11 9l3 1v2a1.5 1.5 0 0 1-1.5 1.5A9 9 0 0 1 4.5 5.5 1.5 1.5 0 0 1 6 4z" fill="#fff"/></svg>0492 158 620</li>
      <li><svg viewBox="0 0 18 18"><rect width="18" height="18" rx="2" fill="#2fa9e0"/><rect x="3.5" y="5" width="11" height="8" fill="none" stroke="#fff" stroke-width="1.2"/><path d="M3.5 5l5.5 4.5L14.5 5" fill="none" stroke="#fff" stroke-width="1.2"/></svg>Dermot@VeloraPixelOutreach.example</li>
      <li><svg viewBox="0 0 18 18"><rect width="18" height="18" rx="2" fill="#2fa9e0"/></svg>in/dermotkalway</li>
    </ul>
  </section>

</body>
</html>
```